holloway paving service

Needs to have phone number 0418259730 and email markholloway@brightmail.com.au.
ABN 62318470915
name mark holloway

For all your concreting solutions
Excavation
Exposed & colour concrete
House & shed slabs
Driveways
Landing & steps

Contact Information for Business Card

ph 0418259730
email markholloway@brightmail.com.au.
ABN 62318470915
name mark holloway

```html
<!DOCTYPE html>
<html lang="en">
<head>
<meta charset="utf-8">
<title>Holloway Paving Service – Business Card</title>
<link rel="stylesheet" href="https://fonts.googleapis.com/css2?family=Roboto+Condensed:wght@400;700&family=Roboto:wght@400;500&display=swap">
<style>
  :root{
    --bg:#e4e2df;
    --orange:#ec6a22;
    --orange-light:#f07a35;
    --paper:#f3f3f2;
    --slate:#5e5f61;
    --slate-dark:#4f5052;
    --ink:#55575a;
    --white:#ffffff;
  }
  *{margin:0;padding:0;box-sizing:border-box}
  html,body{width:1200px;height:886px;overflow:hidden;background:var(--bg)}
  .stage{position:relative;width:1200px;height:886px;display:flex;align-items:center;justify-content:center;gap:60px}
  .card{width:520px;height:300px;position:relative;overflow:hidden;box-shadow:0 6px 18px rgba(0,0,0,.18)}

  /* front */
  .card-front{display:flex}
  .front-brand{width:50%;background:var(--paper);display:flex;align-items:center;padding-left:34px;gap:14px}
  .brand-square{width:34px;height:34px;background:var(--orange);flex:none}
  .brand-divider{width:1.5px;height:70px;background:var(--orange);flex:none}
  .brand-text{font-family:"Roboto Condensed",sans-serif;color:var(--orange)}
  .brand-name{font-weight:700;font-size:17px;line-height:1.15;text-transform:uppercase;letter-spacing:.2px}
  .brand-phone{font-family:"Roboto",sans-serif;font-size:13px;margin-top:5px;letter-spacing:.6px}

  .front-contact{width:50%;background:linear-gradient(90deg,var(--orange-light),var(--orange));color:var(--white);padding:74px 0 0 30px}
  .person-name{font-family:"Roboto Condensed",sans-serif;font-weight:700;font-size:24px;text-transform:uppercase;letter-spacing:.3px;margin-bottom:10px}
  .contact-list{list-style:none;font-family:"Roboto",sans-serif;font-size:12.5px;line-height:20px}
  .contact-list li{display:flex;align-items:center;gap:8px}
  .contact-list svg{width:11px;height:11px;flex:none}
  .abn{padding-left:19px}

  /* back */
  .card-back{background:linear-gradient(135deg,var(--slate),var(--slate-dark));display:flex;flex-direction:column;align-items:center;padding-top:62px}
  .back-brand{display:flex;align-items:center;gap:12px;font-family:"Roboto Condensed",sans-serif;font-weight:700;font-size:22px;color:var(--white);text-transform:uppercase;letter-spacing:.4px}
  .back-brand .brand-square{width:30px;height:30px}
  .services{list-style:none;margin-top:34px;font-family:"Roboto",sans-serif;font-size:14px;line-height:22px;color:var(--white)}
  .services li{display:flex;align-items:center;gap:10px}
  .services li::before{content:"";width:5px;height:5px;border-radius:50%;background:var(--orange);flex:none}
</style>
</head>
<body>
<main class="stage">
  <section class="card card-front" aria-label="Business card front">
    <div class="front-brand">
      <span class="brand-square"></span>
      <span class="brand-divider"></span>
      <div class="brand-text">
        <div class="brand-name">Holloway Paving<br>Service</div>
        <div class="brand-phone">0418259730</div>
      </div>
    </div>
    <div class="front-contact">
      <h1 class="person-name">Mark Holloway</h1>
      <ul class="contact-list">
        <li><svg viewBox="0 0 12 12" aria-hidden="true"><path fill="#fff" d="M2.5 1l2 2-1 1.3c.6 1.5 1.7 2.6 3.2 3.2L8 6.5l2 2-1.2 1.8C5 10 2 7 1.7 2.2z"/></svg>0418259730</li>
        <li><svg viewBox="0 0 12 12" aria-hidden="true"><rect x="1" y="2.5" width="10" height="7" fill="#fff"/><path d="M1 2.5l5 4 5-4" stroke="#ec6a22" fill="none"/></svg>markholloway@brightmail.com.au</li>
        <li><svg viewBox="0 0 12 12" aria-hidden="true"><circle cx="6" cy="6" r="5" fill="#fff"/><path d="M1 6h10M6 1c-2.5 3-2.5 7 0 10M6 1c2.5 3 2.5 7 0 10" stroke="#ec6a22" stroke-width=".8" fill="none"/></svg>www.hollowaypaving.com.au</li>
        <li class="abn">ABN 62318470915</li>
      </ul>
    </div>
  </section>

  <section class="card card-back" aria-label="Business card back">
    <div class="back-brand"><span class="brand-square"></span>Holloway Paving Service</div>
    <ul class="services">
      <li>Excavation</li>
      <li>Exposed &amp; colour concrete</li>
      <li>House &amp; shed slabs</li>
      <li>Driveways</li>
      <li>Landing &amp; steps</li>
    </ul>
  </section>
</main>
</body>
</html>
```